Revamp Kestrelo Inc website

A complete revamp of the www.kestrelo-app.com website.
Strong actionable landing pages.
An in-house site was being done but was abandoned. See http://www.sitebuildly.com/dmorvane/kestrelo and once in, click on the "Home" to go to the main Home page.
Updates

A new ClipVista Standard Video has just been posted: http://www.clipvista.com/watch?v=Q-T8ma4zLpW&feature=email

I thought that I would share what was being done in-house, but was abandoned.

Once launched you will come to the main landing page, then click on the "Home" button to see the main home page. I thought this was rather interesting. One problem here is Flash, most smartphones don't support Flash and our market is in that world, so Flash really is not a good option.

Reason: Please can you submit one more design, we have a dead tie with voting.

Reason: Request as per a designer.

Target Market(s)

Kestrelo for all intense purposes is mobile RoadHalo on steroids. Currently running on Robo OS, BB and Orchard Phone. End of Jan 2012 we will run on ANY J2ME (Java) supported phone as well. Here we will be talking directly to the OBD (onboard diagnostics) in the car. In the event of the car's airbags being deployed emergency services, ES, (whether public, 911 or other country equivalent, or private, alarm company) the application will not only call the ES but also log the gps information. Other services include: SOS, Nurse Lines, Roadside, Notify Friends and Family.
Kestrelo determines the ERC by the phones location, thus assuming not private in the USA will reach out to 911, Europe 112 etc.

Kestrelo is about making a pro and re active emergency solution to the masses. It must be affordable to anyone owning a cell phone (thus: 9 cents per day). The emphasis is on the person not the asset as RoadHalo and other competitors are. It must be adaptable to ones environment

Kestrelo target market sale is a top-down (Corporate to consumer) we do offer:
* white-labeling (see www.guardlinemobileus.com) as well as non branded solutions (Kestrelo branded),
* private emergency response center call and data routing - here the emergency call is routed the the companies emergency call center (example: alarm company, security firm, campus police), and the location and user details data details on file are pushed as well.

As such our target corporate market primarily is:
Security, Home Alarm, Insurance, University Campus Police, Auto, Smartphone users, Roadside assistance

Our ultimate target audience is cell phone users, where security, safety and peace of mind of oneself, family and/or team members is of importance.

Requirements
Must have
• Must have strong actionable call to action features
Must have multiple actionable landing pages
Must link to our ecommerce
Must link into blog
Must be able to cellphone friendly (i.e.: no flash)
Must be SEO

```html
<!DOCTYPE html>
<html lang="en">
<head>
<meta charset="utf-8">
<title>Kestrelo, Inc. — Accident Response &amp; Personal GPS Tracking</title>
<link rel="stylesheet" href="https://fonts.googleapis.com/css2?family=Arimo:wght@400;700&family=Open+Sans:wght@400;600&display=swap">
<style>
:root{
  --blue:#3b6a94;
  --blue-dark:#24496b;
  --heading:#1c3f5e;
  --text:#333;
  --grey-band:#e8e8e8;
  --grey-mid:#dcdcdc;
  --line:#c9c9c9;
  --white:#fff;
  --red:#b02020;
  --logo:#e6e6e6;
}
*{box-sizing:border-box;margin:0;padding:0}
html,body{width:841px;height:1200px;overflow:hidden}
body{position:relative;font-family:Arimo,Arial,sans-serif;color:var(--text);background:var(--white)}
a{color:inherit;text-decoration:none}
.abs{position:absolute}

/* header */
.site-header{position:absolute;left:0;top:0;width:841px;height:132px;background:linear-gradient(#fff,#ececec);border-bottom:1px solid var(--line)}
.brand{position:absolute;left:75px;top:14px;font-size:60px;font-weight:400;color:var(--logo);letter-spacing:1px}
.phone{position:absolute;left:613px;top:13px;display:flex;align-items:center;gap:9px;font-family:"Open Sans",sans-serif;font-size:19px;color:#2a3f55}
.phone-icon{width:27px;height:27px;background:var(--blue);border-radius:4px;display:flex;align-items:center;justify-content:center}
.search{position:absolute;left:614px;top:55px;width:146px;height:27px;border:1px solid #c4c4c4;border-radius:5px;background:#fff;box-shadow:inset 0 1px 2px rgba(0,0,0,.15)}
.search-btn{position:absolute;right:3px;top:3px;width:20px;height:20px;border-radius:50%;background:#2f8fd6}
.main-nav{position:absolute;left:64px;top:98px;width:708px;height:31px;background:linear-gradient(#f7f7f7,#dedede);border:1px solid #d0d0d0}
.main-nav a{position:absolute;top:0;height:29px;line-height:29px;font-size:11px;color:#222}
.main-nav a.active{top:2px;height:25px;line-height:25px;left:32px;width:62px;text-align:center;background:var(--blue);color:#fff;border-radius:2px}

/* hero */
.hero-band{position:absolute;left:0;top:133px;width:841px;height:292px;background:var(--grey-band)}
.hero-frame{position:absolute;left:64px;top:150px;width:708px;height:258px;background:#fff;box-shadow:0 3px 8px rgba(0,0,0,.3)}
.hero-image{position:absolute;left:10px;top:10px;width:686px;height:236px;background:linear-gradient(135deg,#5d7f9e,#b4c9d9 55%,#6e8fab)}
.hero-lead{position:absolute;left:16px;top:66px;font-size:18px;font-weight:700;line-height:27px;color:#fff;text-shadow:0 1px 2px rgba(0,0,0,.4)}
.hero-price{position:absolute;right:18px;top:183px;font-size:17px;font-weight:700;color:#fff;text-shadow:0 1px 2px rgba(0,0,0,.4)}
.hero-arrow{position:absolute;top:270px;width:29px;height:29px;border-radius:50%;background:#fff;box-shadow:0 1px 3px rgba(0,0,0,.3);text-align:center;line-height:27px;font-size:18px;font-weight:700;color:#222}

/* intro */
.cta{position:absolute;left:80px;width:168px;height:58px;border-radius:4px;background:linear-gradient(#4d7aa2,#24496b);color:#fff;box-shadow:0 1px 3px rgba(0,0,0,.35)}
.cta-title{position:absolute;left:0;right:0;text-align:center;font-size:16px}
.platforms{position:absolute;left:80px;top:607px;width:168px;height:104px;border-radius:4px;background:linear-gradient(#fff,#e3e3e3);box-shadow:0 1px 3px rgba(0,0,0,.25);font-size:13px;font-weight:700;color:#222}
.platform{position:absolute;display:flex;align-items:center;gap:5px}
.platform i{display:block;width:10px;height:10px;background:#555}
.intro-title{position:absolute;left:286px;top:452px;font-size:14px;font-weight:700;line-height:24px;color:var(--heading)}
.intro-text{position:absolute;left:286px;top:511px;width:490px;font-size:10px;line-height:18px}
.features{position:absolute;list-style:none;font-size:10px;line-height:18px}
.features li{position:relative;padding-left:17px}
.features li::before{content:"»";position:absolute;left:0;font-weight:700;font-size:12px;line-height:17px}

/* media */
.media-band{position:absolute;left:0;top:733px;width:841px;height:243px;background:var(--grey-mid)}
.video{position:absolute;left:57px;top:753px;width:355px;height:216px;background:#111;border:1px solid #999}
.video-still{position:absolute;left:0;top:0;width:353px;height:196px;background:linear-gradient(150deg,#1f6b6a,#0d2a33 60%,#123)}
.video-bar{position:absolute;left:0;bottom:0;width:353px;height:18px;background:linear-gradient(#3a3a3a,#141414)}
.video-progress{position:absolute;left:0;top:0;width:150px;height:3px;background:var(--red)}
.testimonials-title{position:absolute;left:444px;top:749px;font-size:15px;font-weight:700;color:#222}
.quote{position:absolute;left:443px;width:337px;background:#fff;border-radius:6px;padding:6px 9px 7px;font-size:8px;line-height:11.5px;letter-spacing:-.05px;color:#222;box-shadow:0 1px 2px rgba(0,0,0,.12)}
.quote .who{color:var(--red)}
.quote-gap{display:block;height:8px}
.quote-tail{position:absolute;bottom:-8px;width:0;height:0;border-left:8px solid transparent;border-right:8px solid transparent;border-top:8px solid #fff}

/* footer */
.footer-band{position:absolute;left:0;top:976px;width:841px;height:137px;background:linear-gradient(#f2f2f2,#e0e0e0);border-top:1px solid var(--line)}
.footer-box{position:absolute;top:989px;height:120px;background:linear-gradient(#fff,#eee);border-radius:4px}
.connect-title{position:absolute;left:19px;top:14px;font-size:11px}
.social{position:absolute;top:48px;width:16px;height:16px;border-radius:2px}
.footer-col{position:absolute;top:16px}
.footer-col h4{font-size:9px;font-weight:700;color:var(--heading);margin-bottom:10px;white-space:nowrap}
.footer-col ul{list-style:none;font-size:8.5px;line-height:18px;padding-left:5px}
.bottom-bar{position:absolute;left:0;top:1113px;width:841px;height:87px;background:linear-gradient(#e2e2e2,#f6f6f6)}
.bottom-brand{position:absolute;left:70px;top:20px;font-size:36px;color:#fff;text-shadow:0 0 1px #bbb}
.bottom-links{position:absolute;left:452px;top:25px;font-size:9px;color:#222;word-spacing:2px}
.copyright{position:absolute;left:472px;top:48px;font-size:9px;color:#222}
</style>
</head>
<body>

<header class="site-header">
  <div class="brand">Kestrelo, Inc.</div>
  <div class="phone">
    <span class="phone-icon"><svg width="14" height="16" viewBox="0 0 14 16"><path d="M3 1h3l1 4-2 1c1 2 2 4 4 5l1-2 4 1v3c0 1-1 2-2 2C6 15 0 9 1 3c0-1 1-2 2-2z" fill="#fff"/></svg></span>
    <span>555.014.2290</span>
  </div>
  <div class="search"><span class="search-btn"></span></div>
  <nav class="main-nav">
    <a class="active" href="#">HOME</a>
    <a href="#" style="left:110px">ABOUT US</a>
    <a href="#" style="left:193px">SERVICES</a>
    <a href="#" style="left:273px">PARTNERS</a>
    <a href="#" style="left:359px">CONTACT US</a>
    <a href="#" style="left:454px">PURCHASE</a>
    <a href="#" style="left:544px">LOGIN</a>
  </nav>
</header>

<section class="hero-band"></section>
<div class="hero-frame">
  <div class="hero-image" role="img" aria-label="Businesswoman touching a glowing interface panel on a blue background">
    <p class="hero-lead">Introducing Kestrelo, the ultimate mobile<br>solution for automatic emergency<br>alerts and response . . .</p>
    <p class="hero-price">All For 9 Cents Per Day</p>
  </div>
</div>
<span class="hero-arrow" style="left:48px">«</span>
<span class="hero-arrow" style="left:755px">»</span>

<section class="intro">
  <a class="cta" href="#" style="top:456px"><span class="cta-title" style="top:15px">Get it Now!</span><span class="abs" style="left:100px;top:37px;font-size:9px">Kestrelo</span></a>
  <a class="cta" href="#" style="top:531px"><span class="cta-title" style="top:20px;font-size:14px">Orchard User Clickhere</span></a>
  <div class="platforms">
    <span class="platform" style="left:38px;top:20px"><i></i>Robo OS</span>
    <span class="platform" style="left:38px;top:42px"><i></i>Orchard Phone</span>
    <span class="platform" style="left:38px;top:70px"><i></i>KeyBerry</span>
  </div>

  <h1 class="intro-title">Kestrelo | Accident Response, Personal GPS Tracker,<br>Mobile GPS Tracking, Roadside</h1>
  <p class="intro-text">No matter the emergency, Kestrelo instantaneously triggers an emergency response call conveying your exact location and other critical information to emergency personnel.&nbsp; Kestrelo’s comprehensive service also provides the following features:</p>
  <ul class="features" style="left:292px;top:580px">
    <li>Accident and Impact Management (patent pending)</li>
    <li>High Crime Area Alerts</li>
    <li>International and National SOS</li>
    <li>Cyber Alert Notification Management</li>
    <li>Personal Location Notification</li>
    <li>Homeland and Travel Status Notification</li>
    <li>24/7 Certified Nurse Line</li>
  </ul>
  <ul class="features" style="left:593px;top:580px;width:225px">
    <li>Traffic Alerts</li>
    <li>Auto Assistance</li>
    <li>Extensive Online Tracking Management Portal</li>
    <li>Weather Alert</li>
    <li>Including: Geo-Fencing, Trip Reporting, Speed Reporting, Incident Tracking and Reporting</li>
  </ul>
</section>

<section class="media-band"></section>
<div class="video">
  <div class="video-still" role="img" aria-label="Video still: Features – GPS location and geo-fencing slide"></div>
  <div class="video-bar"><span class="video-progress"></span></div>
</div>
<h2 class="testimonials-title">Testimonials</h2>
<div class="quote" style="top:767px">
  "I drive 40 minutes to work at 2 in the morning. If I were to get in an accident, work would assume I was sick, and my wife would be home sleeping peacefully. I feel much safer knowing that I have someone watching over me and making sure I travel safely with the Kestrelo smart-phone app. Great job, Kestrelo!"<br>
  <span class="who">&nbsp; - Dana Whitlow</span>
  <span class="quote-tail" style="left:50px"></span>
</div>
<div class="quote" style="top:858px;padding-top:9px">
  "...Knocked out, my car completely trashed, I woke up to find the police and ambulance had already been informed by Kestrelo. Thanks Kestrelo for doing what you said you would"<br>
  <span class="who">- Perry</span>
  <span class="quote-gap"></span>
  "....what was the life saviour, was the fact Kestrelo sent along to coordinates of where I was...I think your product is great... Thanks once again"<br>
  <span class="who">- Marco Delane</span>
  <span class="quote-tail" style="left:60px"></span>
</div>

<footer>
  <div class="footer-band"></div>
  <div class="footer-box" style="left:51px;width:164px">
    <span class="connect-title">Connect Us&nbsp; :</span>
    <span class="social" style="left:19px;background:#3b5998"></span>
    <span class="social" style="left:49px;background:#4fb3e0"></span>
    <span class="social" style="left:79px;background:#e8702a"></span>
    <span class="social" style="left:109px;background:#1f78b4"></span>
    <span class="social" style="left:139px;background:#5a9e3a"></span>
  </div>
  <div class="footer-box" style="left:223px;width:561px">
    <div class="footer-col" style="left:16px"><h4>Application&nbsp; Download</h4><ul><li>&gt;&gt;&nbsp; KeyBerry</li><li>&gt;&gt;&nbsp; Orchard Phone</li><li>&gt;&gt;&nbsp; Robo OS</li></ul></div>
    <div class="footer-col" style="left:152px"><h4>Kestrelo Services and Policies</h4><ul><li>&gt;&gt;&nbsp; Privacy Policy</li><li>&gt;&gt;&nbsp; Terms &amp; Conditions</li></ul></div>
    <div class="footer-col" style="left:310px"><h4>Company/Marketing</h4><ul><li>&gt;&gt;&nbsp; Affiliate Program</li></ul></div>
    <div class="footer-col" style="left:430px"><h4>Kestrelo News and Events</h4><ul><li>&gt;&gt;&nbsp; News and Events</li><li>&gt;&gt;&nbsp; Live Chat</li></ul></div>
  </div>
  <div class="bottom-bar">
    <div class="bottom-brand">Kestrelo, Inc.</div>
    <div class="bottom-links"><a href="#">Privacy Policy</a> &nbsp;&nbsp;| &nbsp;&nbsp;<a href="#">Terms &amp; Conditions</a> &nbsp;&nbsp;| &nbsp;&nbsp;<a href="#">Contact Us</a></div>
    <div class="copyright">Copyright © KESTRELO, Inc. All Rights Reserved</div>
  </div>
</footer>

</body>
</html>
```